Business Cards for IT Consulting Company (Managed Service Provider)

I am looking to have some business cards printed and would like some designs. We are an IT Consulting company based in Vancouver BC. I would like a nice clean and modern look to the cards. I have uploaded all the versions of my logo so parts can be used as needed. Here is a snippit from our website homepage:

Quillbrook Networks Ltd. is an IT Solutions Partner located in Vancouver BC, Canada. We offer IT solutions and support to customers in the greater Vancouver Area. With expertise in Microsoft platforms, as well as Linux and Mac OSX and over 12 years experience in the IT industry, Quillbrook Networks is dedicated to offering our clients top quality service and products. We take pride in the solutions we offer our customers. The greatest compliment a client can give us is to recommend our services.

Quillbrook Networks Ltd. offers a wide range of IT services from onsite service to remote support and managed service solutions. This allows clients to choose the support path that best suits their company’s needs. Supporting many different sized companies from small to enterprise level over the past 12 years Quillbrook Networks has the experience and expertise needed to ensure things run smoothly. Allowing our clients to focus on doing business.

Revolutionizing the way IT services are delivered.

Quillbrook Networks is dedicated to providing our clients with IT solutions that work and grow with them for years to come. This philosophy helps save money in the long run instead of replacing equipment constantly. Far too often IT solutions are not well thought out and while possibly solving the problem at hand, require replacement due to growth or quality within a very short time frame. Quillbrook Networks takes pride in providing solutions that will last and be able to accommodate growth without the need for replacement.

Industry/Entity Type

Information Technology

Contact Information for Business Card

Quillbrook Networks Ltd.
(Employee Name)
Eml: (Employees Email Address)
Web: quillbrook.me
Ph: 604-555-0148

Font styles to use
Serif
Sans Serif

Requirements
Must have
• The Company logo and company colors.
Nice to have
• - Our tag line: "Revolutionizing IT Services" or "Revolutionizing the way IT services are delivered."
• - Also I really like the idea of nature and technology together blending which is sort of where my logo came from so integrating that somehow onto the business cards would be great.

```html
<!DOCTYPE html>
<html lang="en">
<head>
<meta charset="utf-8">
<title>Quillbrook Networks Ltd. – Business Cards</title>
<link rel="stylesheet" href="https://fonts.googleapis.com/css2?family=Montserrat:wght@600&family=Roboto:ital,wght@0,400;0,500;1,400&display=swap">
<style>
  :root {
    --backdrop: #e9e9ea;
    --brand-blue: #1b8fd6;
    --card-blue: #1c91d8;
    --paper: #f5f5f5;
    --ink: #4a4a4c;
    --ink-dark: #333335;
    --rule: #6b6b6d;
    --band-grey: #59595b;
  }
  * { margin: 0; padding: 0; box-sizing: border-box; }
  html, body { width: 1200px; height: 1200px; overflow: hidden; }
  body {
    position: relative;
    background: var(--backdrop);
    font-family: "Roboto", Arial, sans-serif;
    color: var(--ink);
  }

  .card {
    position: absolute;
    width: 713px;
    height: 418px;
    overflow: hidden;
  }

  /* Front */
  .card-front {
    left: 238px; top: 118px;
    background: var(--card-blue);
  }
  .card-front .wordmark {
    position: absolute;
    left: 0; right: 0; top: 178px;
    text-align: center;
    font-family: "Montserrat", Arial, sans-serif;
    font-weight: 600;
    font-size: 42px;
    letter-spacing: 0.5px;
    color: #ffffff;
  }

  /* Back */
  .card-back {
    left: 231px; top: 645px;
    width: 712px; height: 416px;
    background: var(--paper);
  }
  .card-back .wordmark {
    position: absolute;
    left: 38px; top: 72px;
    font-family: "Montserrat", Arial, sans-serif;
    font-weight: 600;
    font-size: 36px;
    color: var(--brand-blue);
  }
  .wordmark-square {
    display: inline-block;
    width: 22px; height: 22px;
    margin-right: 14px;
    background: currentColor;
    vertical-align: 1px;
  }

  .person {
    position: absolute;
    right: 36px; top: 194px;
    text-align: right;
  }
  .person-name {
    font-weight: 500;
    font-size: 25px;
    color: var(--brand-blue);
    line-height: 1.1;
  }
  .person-title {
    font-style: italic;
    font-size: 16px;
    color: var(--ink-dark);
    margin-top: 8px;
  }

  .divider {
    position: absolute;
    left: 37px; top: 244px;
    width: 482px; height: 1px;
    background: var(--rule);
  }

  .contact-list {
    position: absolute;
    left: 37px; top: 276px;
    list-style: none;
    font-size: 18px;
    line-height: 27px;
    color: var(--ink-dark);
  }
  .contact-list li { display: flex; align-items: center; }
  .contact-list svg { width: 18px; height: 18px; margin-right: 18px; fill: var(--brand-blue); }

  .tagline {
    position: absolute;
    right: 36px; top: 299px;
    text-align: right;
    font-size: 18px;
    line-height: 26px;
    color: var(--ink-dark);
  }

  .band-grey {
    position: absolute;
    left: 0; bottom: 0;
    width: 350px; height: 21px;
    background: var(--band-grey);
  }
  .band-blue {
    position: absolute;
    right: 0; bottom: 0;
    width: 386px; height: 50px;
    background: var(--brand-blue);
    clip-path: polygon(32px 0, 100% 0, 100% 100%, 0 100%);
  }
</style>
</head>
<body>

  <section class="card card-front" role="img" aria-label="Front of card: blue background with a subtle light geometric pattern and the company name">
    <div class="wordmark"><span class="wordmark-square"></span>Quillbrook Networks Ltd.</div>
  </section>

  <section class="card card-back">
    <div class="wordmark"><span class="wordmark-square"></span>Quillbrook Networks Ltd.</div>

    <div class="person">
      <p class="person-name">Daniel Harper</p>
      <p class="person-title">Managing Director</p>
    </div>

    <div class="divider"></div>

    <ul class="contact-list">
      <li>
        <svg viewBox="0 0 24 24" aria-hidden="true"><path d="M3 7c0-2 2-3 4-3h10c2 0 4 1 4 3v2h-5V7H8v2H3zM6 11h12l2 9H4zm6 2a3 3 0 1 0 0 6 3 3 0 0 0 0-6z"/></svg>
        604-555-0148
      </li>
      <li>
        <svg viewBox="0 0 24 24" aria-hidden="true"><path d="M12 2a10 10 0 1 0 0 20 10 10 0 0 0 0-20zm6.9 9h-3a15 15 0 0 0-1.4-6 8 8 0 0 1 4.4 6zM12 4c.9 1.3 1.8 3.9 1.9 7h-3.8C10.2 7.9 11.1 5.3 12 4zM9.5 5a15 15 0 0 0-1.4 6h-3a8 8 0 0 1 4.4-6zM5.1 13h3a15 15 0 0 0 1.4 6 8 8 0 0 1-4.4-6zM12 20c-.9-1.3-1.8-3.9-1.9-7h3.8c-.1 3.1-1 5.7-1.9 7zm2.5-1a15 15 0 0 0 1.4-6h3a8 8 0 0 1-4.4 6z"/></svg>
        www.quillbrook.me
      </li>
      <li>
        <svg viewBox="0 0 24 24" aria-hidden="true"><path d="M2 5h20v14H2zm2 2v.5l8 5.5 8-5.5V7zm0 2.9V17h16V9.9l-8 5.5z"/></svg>
        support@quillbrook.me
      </li>
    </ul>

    <p class="tagline">Revolutionizing the way<br>IT services are delivered</p>

    <div class="band-grey"></div>
    <div class="band-blue"></div>
  </section>

</body>
</html>
```